Business Card - Tidal Lanes

Need Business Card design for company named Tidal Lanes. Software development focused mainly on Brindle Orvix & Zelt Apps. I've attached our logo with both a black and white background. Please add trademark symbol to logo when using.

```html
<!DOCTYPE html>
<html lang="en">
<head>
<meta charset="utf-8">
<title>Tidal Lanes — Business Card</title>
<link href="https://fonts.googleapis.com/css2?family=Open+Sans:wght@400;600;700;800&display=swap" rel="stylesheet">
<style>
  :root {
    --page: #ececec;
    --card-dark: #1c1c1c;
    --card-mid: #2e2e2e;
    --band-gold: #f7b21b;
    --band-amber: #f59a1f;
    --rule-red: #b3261e;
    --ink-dark: #1a1a1a;
    --ink-light: #f2f2f2;
    --ink-soft: #d8d8d8;
    --accent-gold: #f5b71c;
  }
  * { margin: 0; padding: 0; box-sizing: border-box; }
  html, body { width: 1200px; height: 720px; overflow: hidden; }
  body {
    background: var(--page);
    font-family: "Open Sans", Arial, sans-serif;
    position: relative;
  }
  .card {
    position: absolute;
    top: 206px;
    width: 540px;
    height: 308px;
    background: radial-gradient(ellipse at 50% 40%, var(--card-mid) 0%, var(--card-dark) 75%);
    box-shadow: 0 6px 18px rgba(0,0,0,0.25);
    overflow: hidden;
  }
  .card--front { left: 40px; }
  .card--back { left: 620px; }

  .name-band {
    position: absolute;
    left: 0; right: 0;
    top: 34px;
    height: 44px;
    background: linear-gradient(90deg, var(--band-gold), var(--band-amber));
    border-top: 2px solid var(--rule-red);
    border-bottom: 2px solid var(--rule-red);
    display: flex;
    align-items: center;
    justify-content: center;
  }
  .name-band__name { font-weight: 800; font-size: 18px; color: var(--ink-dark); }
  .name-band__title { font-weight: 600; font-size: 15px; color: var(--ink-dark); }

  .brand {
    position: absolute;
    left: 34px;
    top: 150px;
    width: 200px;
    display: flex;
    align-items: center;
    gap: 10px;
  }
  .brand__dot {
    width: 16px; height: 16px;
    border-radius: 50%;
    background: var(--accent-gold);
    flex: none;
  }
  .brand__name {
    font-weight: 700;
    font-size: 26px;
    color: var(--ink-light);
    letter-spacing: -0.5px;
  }

  .divider {
    position: absolute;
    left: 262px;
    top: 110px;
    width: 1px;
    height: 150px;
    background: linear-gradient(180deg, transparent, #8a8a8a, transparent);
  }

  .contact {
    position: absolute;
    left: 290px;
    top: 118px;
    list-style: none;
    color: var(--ink-soft);
    font-size: 15px;
  }
  .contact li { display: flex; align-items: center; gap: 8px; height: 26px; }
  .contact svg { width: 14px; height: 14px; fill: var(--accent-gold); flex: none; }
  .contact .contact__address { margin-top: 12px; padding-left: 0; }

  .back-brand {
    position: absolute;
    inset: 0;
    display: flex;
    align-items: center;
    justify-content: center;
    gap: 18px;
  }
  .back-brand__dot {
    width: 34px; height: 34px;
    border-radius: 50%;
    background: var(--accent-gold);
  }
  .back-brand__name {
    font-weight: 700;
    font-size: 52px;
    color: var(--ink-light);
    letter-spacing: -1px;
  }
</style>
</head>
<body>
  <section class="card card--front" aria-label="Business card front">
    <div class="name-band">
      <span class="name-band__name">Your Name,</span>&nbsp;<span class="name-band__title">Title</span>
    </div>

    <div class="brand">
      <span class="brand__dot"></span>
      <span class="brand__name">Tidal Lanes</span>
    </div>

    <div class="divider"></div>

    <ul class="contact">
      <li>
        <svg viewBox="0 0 16 16" aria-hidden="true"><path d="M4 1h8a1 1 0 0 1 1 1v12a1 1 0 0 1-1 1H4a1 1 0 0 1-1-1V2a1 1 0 0 1 1-1zm1 2v8h6V3H5zm3 9.2a.9.9 0 1 0 0 1.8.9.9 0 0 0 0-1.8z"/></svg>
        <span>555-204-6130</span>
      </li>
      <li>
        <svg viewBox="0 0 16 16" aria-hidden="true"><path d="M3 5c0-1.5 2-3 5-3s5 1.5 5 3v1h-2V5H5v1H3V5zm0 3h10l1 5H2l1-5zm3 1.5v2h4v-2H6z"/></svg>
        <span>555-318-7742</span>
      </li>
      <li class="contact__address">
        <span>4210 Harbor Row, Bayline, FL 30071</span>
      </li>
    </ul>
  </section>

  <section class="card card--back" aria-label="Business card back">
    <div class="back-brand">
      <span class="back-brand__dot"></span>
      <span class="back-brand__name">Tidal Lanes</span>
    </div>
  </section>
</body>
</html>
```